Home Staging Company needs business card design

We're a home staging company called Brightly Settled Home Staging. We would like a business card design that includes aqua and gray. Our current logo of house within chair is fine but I find we almost always use the logo in one color. I'll upload images of front and back of our current card and our logo. Note that we have dropped "Solutions" from our company name and don't want to include it on the card.

Target Market(s)

Realtors and homeowners - people interested in selling their homes

Contact Information for Business Card

Marisol Thistlewood
Brightly Settled Home Staging
757-555-0193
www.brightlysettled.com
marisol@brightlysettled.com

Font styles to use
Serif
Script

Requirements
Must have
• My logo and contact details
• UPDATE***
• I forgot to say that the company name should be included on the front of the card somehow.

```html
<!DOCTYPE html>
<html lang="en">
<head>
<meta charset="utf-8">
<title>Brightly Settled Home Staging – Business Card</title>
<link rel="stylesheet" href="https://fonts.googleapis.com/css2?family=Lora:wght@400&family=Questrial&family=Roboto+Condensed:wght@400&display=swap">
<style>
  :root {
    --backdrop: #b9b9b9;
    --aqua-light: #52b1b9;
    --aqua-deep: #1886b0;
    --aqua: #4aafb8;
    --paper: #f4f4f4;
    --paper-shade: #e7e7e7;
    --ink: #333333;
    --ink-soft: #555555;
    --white: #ffffff;
  }
  * { margin: 0; padding: 0; box-sizing: border-box; }
  html, body { width: 1200px; height: 576px; overflow: hidden; }
  body { background: var(--backdrop); position: relative; }

  .card {
    position: absolute;
    top: 138px;
    width: 484px;
    height: 294px;
    border-radius: 16px;
    overflow: hidden;
  }

  /* Front */
  .card-front {
    left: 82px;
    background: linear-gradient(180deg, var(--aqua-light) 0%, var(--aqua-deep) 100%);
    color: var(--white);
  }
  .card-front .faint-disc {
    position: absolute; left: 70px; top: 10px;
    width: 250px; height: 250px; border-radius: 50%;
    background: rgba(255,255,255,0.07);
  }
  .front-name {
    position: absolute; left: 0; right: 0; top: 100px;
    text-align: center;
    font-family: "Lora", serif; font-weight: 400;
    color: var(--white);
  }
  .front-name .line-main { display: block; font-size: 42px; line-height: 1.1; }
  .front-name .line-sub { display: block; font-size: 17px; letter-spacing: 0.42em; margin-top: 6px; }
  .front-web {
    position: absolute; left: 0; right: 0; top: 266px;
    text-align: center;
    font-family: "Questrial", sans-serif; font-size: 13px;
  }

  /* Back */
  .card-back {
    left: 602px;
    background: linear-gradient(180deg, var(--paper) 0%, var(--paper-shade) 100%);
    border-bottom: 4px solid var(--aqua);
  }
  .card-back .faint-disc {
    position: absolute; left: 290px; top: 20px;
    width: 230px; height: 230px; border-radius: 50%;
    background: rgba(0,0,0,0.04);
  }
  .back-brand {
    position: absolute; left: 30px; top: 90px; width: 190px;
    text-align: center;
  }
  .back-brand .brand-dot {
    display: block; width: 52px; height: 52px; border-radius: 50%;
    background: var(--aqua); margin: 0 auto 14px;
  }
  .back-brand .brand-name {
    font-family: "Lora", serif; font-weight: 400; color: var(--aqua);
  }
  .back-brand .line-main { display: block; font-size: 22px; line-height: 1.1; }
  .back-brand .line-sub { display: block; font-size: 10px; letter-spacing: 0.38em; margin-top: 3px; }

  .person { position: absolute; left: 256px; top: 90px; }
  .person-name { font-family: "Roboto Condensed", sans-serif; font-size: 20px; color: var(--ink); }
  .person-name .surname { color: var(--aqua); }
  .person-title { font-family: "Questrial", sans-serif; font-size: 11px; color: var(--ink-soft); margin-top: 4px; }

  .contact-list { list-style: none; position: absolute; left: 258px; top: 146px; }
  .contact-list li {
    display: flex; align-items: center; gap: 8px;
    height: 17px; margin-bottom: 0.5px;
    font-family: "Questrial", sans-serif; font-size: 12.5px; color: var(--ink);
  }
  .contact-list svg { width: 11px; height: 11px; fill: var(--aqua); flex: none; }
</style>
</head>
<body>
  <section class="card card-front">
    <div class="faint-disc"></div>
    <div class="front-name">
      <span class="line-main">Brightly Settled</span>
      <span class="line-sub">HOME STAGING</span>
    </div>
    <div class="front-web">www.brightlysettled.com</div>
  </section>

  <section class="card card-back">
    <div class="faint-disc"></div>
    <div class="back-brand">
      <span class="brand-dot"></span>
      <div class="brand-name">
        <span class="line-main">Brightly Settled</span>
        <span class="line-sub">HOME STAGING</span>
      </div>
    </div>

    <div class="person">
      <div class="person-name">Marisol <span class="surname">Thistlewood</span></div>
      <div class="person-title">Managing Director</div>
    </div>

    <ul class="contact-list">
      <li>
        <svg viewBox="0 0 12 12" aria-hidden="true"><path d="M1 3c0-1 1-2 5-2s5 1 5 2v1H8V3H4v1H1z"/><rect x="2" y="5" width="8" height="6" rx="1"/></svg>
        757-555-0193
      </li>
      <li>
        <svg viewBox="0 0 12 12" aria-hidden="true"><path d="M6 0.5a5.5 5.5 0 1 0 0 11a5.5 5.5 0 1 0 0-11zm0 1.2c.6.7 1.1 1.9 1.2 3.3H4.8c.1-1.4.6-2.6 1.2-3.3zM4.8 7h2.4c-.1 1.4-.6 2.6-1.2 3.3C5.4 9.6 4.9 8.4 4.8 7zM1.8 5h2c0-1.1.3-2.2.7-3A4.3 4.3 0 0 0 1.8 5zm6.4 0h2A4.3 4.3 0 0 0 7.5 2c.4.8.7 1.9.7 3zM1.8 7a4.3 4.3 0 0 0 2.7 3c-.4-.8-.7-1.9-.7-3zm6.4 0c0 1.1-.3 2.2-.7 3a4.3 4.3 0 0 0 2.7-3z"/></svg>
        www.brightlysettled.com
      </li>
      <li>
        <svg viewBox="0 0 12 12" aria-hidden="true"><path d="M0.5 2.5h11v7h-11z M1 3l5 4 5-4" fill="var(--aqua)"/><path d="M1 3.2l5 3.8 5-3.8" fill="none" stroke="#f4f4f4" stroke-width="1"/></svg>
        marisol@brightlysettled.com
      </li>
    </ul>
  </section>
</body>
</html>
```